Business Card Design

Velora Pixel Outreach

An online marketing consulting & strategy business for the cosmetic niche

We specialise in Increasing Leads, Conversions & Content Marketing

I am looking for a very clean, BOLD business card that is simple & effective

Target Market(s)

cosmetic surgeons & cosmetic clinics

Industry/Entity Type

Marketing

Contact Information for Business Card

Dermot Kalway
Online Marketing Strategist

Dermot@VeloraPixelOutreach.example
0492 158 620

Profile: in/dermotkalway

```html
<!DOCTYPE html>
<html lang="en">
<head>
<meta charset="utf-8">
<title>Velora Pixel Outreach – Business Card</title>
<link rel="stylesheet" href="https://fonts.googleapis.com/css2?family=Lato:wght@400;700;900&display=swap">
<style>
  :root {
    --bg: #e9e6df;
    --card: #ffffff;
    --ink: #5a5c60;
    --ink-dark: #3f4145;
    --blue: #1fa3c8;
    --green: #8dc63f;
    --faint: #e6f1f3;
  }
  * { box-sizing: border-box; margin: 0; padding: 0; }
  html, body { width: 1200px; height: 1000px; overflow: hidden; }
  body {
    background: var(--bg);
    font-family: "Lato", sans-serif;
    position: relative;
  }
  .card {
    position: absolute;
    left: 220px;
    width: 760px;
    height: 434px;
    background: var(--card);
    box-shadow: 0 10px 26px rgba(0,0,0,.18);
    overflow: hidden;
  }
  .card--front { top: 48px; }
  .card--back { top: 518px; }
  .edge { position: absolute; width: 8px; height: 50%; }
  .edge--left-top { left: 0; top: 0; background: var(--blue); }
  .edge--left-bottom { left: 0; bottom: 0; background: var(--green); }
  .edge--right-top { right: 0; top: 0; background: var(--blue); }
  .edge--right-bottom { right: 0; bottom: 0; background: var(--green); }

  .brand { display: flex; align-items: center; }
  .brand__dot { border-radius: 50%; background: var(--blue); flex: none; }
  .brand__name {
    color: var(--ink);
    font-weight: 700;
    text-transform: uppercase;
    letter-spacing: .12em;
    line-height: .95;
  }

  .card--front .brand { position: absolute; left: 110px; top: 112px; }
  .card--front .brand__dot { width: 130px; height: 130px; margin-right: 30px; }
  .card--front .brand__name { font-size: 52px; }
  .front__tagline {
    position: absolute; left: 0; right: 0; top: 300px;
    text-align: center;
    color: var(--blue);
    font-weight: 700;
    font-size: 19px;
  }
  .front__tagline .amp { color: var(--green); }

  .card--back .brand { position: absolute; left: 60px; top: 70px; }
  .card--back .brand__dot { width: 58px; height: 58px; margin-right: 16px; }
  .card--back .brand__name { font-size: 22px; }
  .back__divider {
    position: absolute; left: 355px; top: 50px;
    width: 2px; height: 110px; background: var(--green);
  }
  .back__focus {
    position: absolute; left: 385px; top: 68px;
    color: var(--blue); font-weight: 900; font-size: 22px; line-height: 1.25;
  }
  .back__mark {
    position: absolute; right: -40px; top: 150px;
    width: 330px; height: 330px; border-radius: 50%;
    background: var(--faint);
  }
  .person { position: absolute; left: 60px; top: 212px; }
  .person__name { color: var(--blue); font-weight: 900; font-size: 32px; }
  .person__role { color: var(--ink-dark); font-weight: 700; font-size: 20px; margin-top: 2px; }
  .person__rule { width: 320px; height: 2px; background: var(--green); margin-top: 12px; }

  .contacts { position: absolute; left: 60px; top: 325px; list-style: none; }
  .contacts li {
    display: flex; align-items: center;
    color: var(--ink-dark); font-weight: 700; font-size: 19px;
    height: 30px;
  }
  .contacts svg { width: 20px; height: 20px; margin-right: 12px; flex: none; }
  .contacts .label { color: var(--green); margin-right: 6px; }
</style>
</head>
<body>

<section class="card card--front" aria-label="Business card front">
  <span class="edge edge--left-top"></span>
  <span class="edge edge--left-bottom"></span>
  <span class="edge edge--right-top"></span>
  <span class="edge edge--right-bottom"></span>
  <div class="brand">
    <span class="brand__dot"></span>
    <span class="brand__name">Velora<br>Pixel<br>Outreach</span>
  </div>
  <p class="front__tagline">Online Marketing Consulting <span class="amp">&amp;</span> Strategy Business For The Cosmetic Niche</p>
</section>

<section class="card card--back" aria-label="Business card back">
  <span class="edge edge--left-top"></span>
  <span class="edge edge--left-bottom"></span>
  <span class="edge edge--right-top"></span>
  <span class="edge edge--right-bottom"></span>
  <span class="back__mark"></span>
  <div class="brand">
    <span class="brand__dot"></span>
    <span class="brand__name">Velora<br>Pixel<br>Outreach</span>
  </div>
  <span class="back__divider"></span>
  <p class="back__focus">Specialized in Increasing Leads,<br>Conversions &amp; Content Marketing</p>

  <div class="person">
    <p class="person__name">Dermot Kalway</p>
    <p class="person__role">Online Marketing Strategist</p>
    <div class="person__rule"></div>
  </div>

  <ul class="contacts">
    <li>
      <svg viewBox="0 0 20 20" aria-hidden="true"><path fill="#1fa3c8" d="M5 2l3 4-2 2c1 2.5 3.5 5 6 6l2-2 4 3-2 3C9 18 2 11 2 4z"/></svg>
      0492 158 620
    </li>
    <li>
      <svg viewBox="0 0 20 20" aria-hidden="true"><rect x="2" y="2" width="16" height="16" rx="2" fill="#1fa3c8"/></svg>
      <span class="label">Profile:</span> in/dermotkalway
    </li>
    <li>
      <svg viewBox="0 0 20 20" aria-hidden="true"><rect x="2" y="4" width="16" height="12" fill="#1fa3c8"/><path d="M2 4l8 7 8-7" fill="none" stroke="#fff" stroke-width="1.5"/></svg>
      Dermot@VeloraPixelOutreach.example
    </li>
  </ul>
</section>

</body>
</html>
```